BOLD & MINIMALIST DESIGN NEEDED

We want a very bold but minimalistic business card design that is impactful and utilizes both sides of the business card. Our current logo is included for your use.

We want bold fonts and good use of negative space. We don't want the logo to overpower the design.

Target Market(s)

Professionals who are building new commercial buildings.

Industry/Entity Type

Construction

Contact Information for Business Card

Name, Title, email, office phone, cell phone, website

Font styles to use
Serif
Sans Serif

Requirements
Must have
• Bold design!

```html
<!DOCTYPE html>
<html lang="en">
<head>
<meta charset="utf-8">
<title>Ridgeline Design + Build — Business Card</title>
<link rel="stylesheet" href="https://fonts.googleapis.com/css2?family=Montserrat:wght@400;600;800&family=Oswald:wght@700&display=swap">
<style>
  :root {
    --ink: #1b1b1b;
    --paper: #ffffff;
    --lime: #7cc42a;
    --stage: #e6e6e6;
    --back-tone: #222222;
  }
  * { box-sizing: border-box; margin: 0; padding: 0; }
  html, body {
    width: 1200px; height: 900px; overflow: hidden;
    background: var(--stage);
    font-family: "Montserrat", Arial, sans-serif;
  }
  .sheet {
    width: 1200px; height: 900px;
    display: flex; flex-direction: column; align-items: center; justify-content: center;
    gap: 36px;
  }
  .card {
    position: relative;
    width: 700px; height: 400px;
    overflow: hidden;
    box-shadow: 0 10px 30px rgba(0,0,0,.25);
  }
  .card--front { background: var(--paper); }
  .card__waves { position: absolute; inset: 0; width: 100%; height: 100%; }

  .brand {
    position: absolute; left: 60px; top: 58px;
    display: flex; align-items: center; gap: 12px;
    color: var(--ink);
    font-weight: 800; font-size: 26px; letter-spacing: .5px; text-transform: uppercase;
  }
  .brand__mark { width: 18px; height: 18px; background: var(--ink); }

  .holder {
    position: absolute; right: 70px; top: 190px; text-align: right;
  }
  .holder__name {
    font-family: "Oswald", "Arial Narrow", sans-serif;
    font-weight: 700; font-size: 30px; line-height: 1; letter-spacing: .5px;
    color: var(--lime); text-transform: uppercase;
  }
  .holder__title {
    margin-top: 5px;
    color: var(--paper); font-size: 13px; letter-spacing: 1.5px; text-transform: uppercase;
  }
  .contacts {
    position: absolute; right: 70px; top: 252px;
    list-style: none; text-align: right; color: var(--paper);
    font-size: 13px; line-height: 20px;
  }
  .contacts li { display: flex; justify-content: flex-end; align-items: center; gap: 8px; }
  .contacts svg { width: 12px; height: 12px; fill: none; stroke: var(--lime); stroke-width: 1.6; }
  .contacts .accent { color: var(--lime); }

  .card--back { background: var(--ink); }
  .back__pattern {
    position: absolute; inset: 0;
    background: linear-gradient(135deg, #262626 0%, var(--back-tone) 50%, #1a1a1a 100%);
  }
  .back__brand {
    position: absolute; right: 44px; bottom: 36px;
    display: flex; align-items: center; gap: 10px;
    color: var(--paper);
    font-weight: 800; font-size: 15px; letter-spacing: .5px; text-transform: uppercase;
  }
  .back__brand .brand__mark { width: 12px; height: 12px; background: var(--lime); }
</style>
</head>
<body>
<main class="sheet">

  <section class="card card--front" aria-label="Business card front">
    <svg class="card__waves" viewBox="0 0 700 400" preserveAspectRatio="none" aria-hidden="true">
      <path d="M0,236 C100,258 200,254 270,226 C200,246 100,252 0,252 Z" fill="#1b1b1b"/>
      <path d="M0,272 C130,277 240,262 320,212 C400,162 540,102 680,78 C540,118 400,178 320,230 C240,282 130,292 0,290 Z" fill="#7cc42a"/>
      <path d="M0,300 C130,305 240,290 320,240 C400,190 540,130 700,100 L700,400 L0,400 Z" fill="#1b1b1b"/>
    </svg>

    <div class="brand"><span class="brand__mark"></span>Ridgeline Design + Build</div>

    <div class="holder">
      <h1 class="holder__name">Marcus Hale</h1>
      <p class="holder__title">Owner</p>
    </div>

    <ul class="contacts">
      <li>(555) 014-2290
        <svg viewBox="0 0 12 12"><path d="M2 1.5h2.2l1 2.6-1.3.9a6 6 0 0 0 3.1 3.1l.9-1.3 2.6 1v2.2A1 1 0 0 1 9.5 11 8.5 8.5 0 0 1 1 2.5a1 1 0 0 1 1-1z"/></svg></li>
      <li>(555) 014-2291
        <svg viewBox="0 0 12 12"><rect x="1.5" y="4.5" width="9" height="6" rx="1"/><path d="M1 4a5 3 0 0 1 10 0"/><circle cx="6" cy="7.5" r="1.3"/></svg></li>
      <li>hello@ridgelinebuild.com
        <svg viewBox="0 0 12 12"><rect x="1" y="2.5" width="10" height="7"/><path d="M1 2.5l5 4 5-4"/></svg></li>
      <li><span>www.<span class="accent">ridgelinebuild</span>.com</span>
        <svg viewBox="0 0 12 12"><circle cx="6" cy="6" r="5"/><path d="M1 6h10M6 1c-2.5 3-2.5 7 0 10M6 1c2.5 3 2.5 7 0 10"/></svg></li>
    </ul>
  </section>

  <section class="card card--back" aria-label="Business card back">
    <div class="back__pattern" role="img" aria-label="Tonal repeated monogram pattern across the dark card back"></div>
    <div class="back__brand"><span class="brand__mark"></span>Ridgeline</div>
  </section>

</main>
</body>
</html>
```